Product label for herbal salves, lotions, soaps and tinctures

We need a very simple, clean and organic looking label that can be used for an ointment jar, a lotion bottle and a dropper bottle.
We have an existing logo (see attached). We like the colors white, olive green, gold and black. It needs to include product name as dominant and logo. It also needs to include an ingredient list, and usage statement. Include weight of product, distributed by, made in the USA, and QVX statement.
Example of what needs to be present:
Logo
Name: Tranquil Ease Blend
Used for: For Muscle Aches, Arthritis, Tendonitis, Headaches
To Use: For muscle aches, arthritis and tendonitis, massage into affected area. For tension headache apply to neck, temples and forehead.
Store in a cool and dry place, away from direct heat and sunlight.
Weight of product: 1.75
DIST. BY: Copper Brook Herbal
Made in the USA
This product is not intended to diagnose, treat, cure
or prevent any disease. Not regulated
by the QVX. Please consult your health care practitioner
before using product. Discontinue use if any adverse reaction occurs.
Ingredient list:
Wildcrafted Ingredients:
Ashwagandha Root, Peppermint Leaf, Hops Flowers, St. John’s Wort Herb, Arnica Flowers, Green Tea Leaf, Alfalfa Leaf, Dandelion Root, Burdock Root, Chickweed Herb, Chaparral Leaf, Yarrow Flowers, Boneset Herb, Moringa Leaf, Meadowsweet Herb, Nettle Leaf
Organic Ingredients:
Olive Oil, Aloe Leaf, Sweet Birch Bark, Helichrysum Flowers, Holy Basil Leaf, Borage Herb, Ginger Root, Angelica Root, White Willow Bark, Mustard Seed, Beeswax, Vitamin E, Essential Oils
Dimensions of Jar:
Circumference: 7 in.
Height: 1 in.

```html
<!DOCTYPE html>
<html lang="en">
<head>
<meta charset="utf-8">
<title>Tranquil Ease Blend – Jar Label</title>
<link rel="stylesheet" href="https://fonts.googleapis.com/css2?family=Montserrat:wght@400;600&family=Noto+Serif:wght@400;700&display=swap">
<style>
  :root {
    --backdrop: #6b6b1e;
    --olive: #6f7431;
    --olive-dark: #5d6226;
    --gold: #c9a24a;
    --gold-light: #ecd58e;
    --copper: #8a5a22;
    --paper: #ffffff;
    --leaf-tint: #e4ead3;
    --ink-light: #ffffff;
  }
  * { margin: 0; padding: 0; box-sizing: border-box; }
  html, body { width: 1200px; height: 1000px; overflow: hidden; }
  body {
    background: var(--backdrop);
    position: relative;
    font-family: "Montserrat", sans-serif;
  }
  .label {
    position: absolute;
    left: 40px;
    top: 410px;
    width: 1120px;
    height: 180px;
    background: var(--paper);
    box-shadow: 0 14px 22px rgba(0,0,0,0.35);
    overflow: hidden;
  }
  .leaf-artwork {
    position: absolute;
    inset: 0;
    background:
      radial-gradient(ellipse 180px 110px at 700px 70px, var(--leaf-tint), transparent 70%),
      radial-gradient(ellipse 160px 100px at 400px 120px, var(--leaf-tint), transparent 70%),
      radial-gradient(ellipse 170px 100px at 980px 140px, var(--leaf-tint), transparent 70%),
      linear-gradient(90deg, #f4f6ee, #fbfcf8 50%, #f4f6ee);
  }
  .rule {
    position: absolute;
    left: 0; right: 0;
    height: 3px;
    background: linear-gradient(90deg, var(--copper), var(--gold-light) 50%, var(--copper));
  }
  .rule.top { top: 6px; }
  .rule.bottom { bottom: 6px; }
  .panel {
    position: absolute;
    top: 12px;
    bottom: 12px;
    background: var(--olive);
    color: var(--ink-light);
  }
  .panel.ingredients {
    left: 5px;
    width: 290px;
    padding: 16px 12px;
    font-size: 7.6px;
    line-height: 1.3;
  }
  .panel.ingredients h3 {
    font-size: 7.6px;
    font-weight: 600;
    text-transform: uppercase;
  }
  .panel.ingredients .usage { margin-top: 12px; }
  .panel.details {
    right: 5px;
    width: 280px;
    padding: 10px 12px 9px;
    font-size: 7.3px;
    line-height: 1.3;
    display: flex;
    flex-direction: column;
  }
  .panel.details .product-title {
    font-size: 15px;
    font-weight: 600;
    line-height: 1.2;
    margin-bottom: 4px;
  }
  .panel.details .store { margin-top: 3px; }
  .panel.details .footer {
    margin-top: auto;
    display: flex;
    align-items: flex-end;
    gap: 8px;
  }
  .panel.details .footer .brand-small {
    font-family: "Noto Serif", serif;
    font-weight: 700;
    font-size: 11px;
    line-height: 1.1;
    width: 86px;
    flex-shrink: 0;
  }
  .centre {
    position: absolute;
    left: 300px;
    right: 290px;
    top: 18px;
    text-align: center;
    font-family: "Noto Serif", serif;
  }
  .brand-name {
    color: var(--olive);
    font-weight: 700;
    font-size: 22px;
    line-height: 1.05;
  }
  .brand-rule {
    width: 290px;
    height: 2px;
    margin: 8px auto 4px;
    background: linear-gradient(90deg, transparent, var(--gold) 20%, var(--copper) 50%, var(--gold) 80%, transparent);
  }
  .product-name {
    color: var(--olive);
    font-size: 31px;
    font-weight: 400;
    line-height: 1.15;
  }
  .uses {
    color: var(--olive-dark);
    font-size: 9.5px;
    margin-top: 4px;
  }
</style>
</head>
<body>
  <div class="label">
    <div class="leaf-artwork" role="img" aria-label="Pale green botanical line drawing of leafy herb stems"></div>
    <div class="rule top"></div>
    <div class="rule bottom"></div>

    <section class="panel ingredients">
      <h3>Wildcrafted Ingredients:</h3>
      <p>Ashwagandha Root, Peppermint Leaf, Hops Flowers, St. John’s Wort Herb, Arnica Flowers, Green Tea Leaf, Alfalfa Leaf, Dandelion Root, Burdock Root, Chickweed Herb, Chaparral Leaf, Yarrow Flowers, Boneset Herb, Moringa Leaf, Meadowsweet Herb, Nettle Leaf</p>
      <h3>Organic Ingredients:</h3>
      <p>Olive Oil, Aloe Leaf, Sweet Birch Bark, Helichrysum Flowers, Holy Basil Leaf, Borage Herb, Ginger Root, Angelica Root, White Willow Bark, Mustard Seed, Beeswax, Vitamin E, Essential Oils</p>
      <div class="usage">
        <h3>To Use:</h3>
        <p>For muscle aches, arthritis and tendonitis, massage into affected area. For tension headache apply to neck, temples and forehead.</p>
      </div>
    </section>

    <div class="centre">
      <div class="brand-name">Copper Brook Herbal</div>
      <div class="brand-rule"></div>
      <h1 class="product-name">Tranquil Ease Blend</h1>
      <p class="uses">For Muscle Aches. Arthritis. Tendonitis.&nbsp; Headaches</p>
    </div>

    <section class="panel details">
      <h2 class="product-title">Tranquil Ease Blend</h2>
      <p>MADE IN THE USA</p>
      <p>This product is not intended to diagnose, treat, cure or prevent any disease. Not regulated by the QVX. Please consult your health care practitioner before using product. Discontinue use if any adverse reaction occurs.</p>
      <p class="store">Store in a cool and dry place, away from direct heat and sunlight.</p>
      <div class="footer">
        <div class="brand-small">Copper Brook<br>Herbal</div>
        <div>Weight of product: 1.75<br>DIST. BY: Copper Brook Herbal</div>
      </div>
    </section>
  </div>
</body>
</html>
```